Expedition Cruise Sales Website for the Polar Regions (Antarctica & Arctic)

This will be a website for selling cruises.
This site should have a homepage, a ship page, destinations, and itineraries.
I have created a file specifying each page, and it is attached.
Pages:
1. Home
2. Cruise Lines
- 2.1 Ships
3. Destinations
- 3.1 Region - 3.2 Country - 3.3 City
4. Itineraries
- 4.1 Itinerary
5. Blog / Travel Tips 6. About Us
7. Contact
Please take a look on the attached pdf
Target Market(s)
Expedition Travelers
Coding
Coded - Design and coding required
Number of Pages Required
5+ page
Font styles to use
Look and feel
Each slider illustrates characteristics of the customer's brand and the style your logo design should communicate.

```html
<!DOCTYPE html>
<html lang="en">
<head>
<meta charset="utf-8">
<title>Polarine – Expedition Cruises</title>
<link rel="stylesheet" href="https://fonts.googleapis.com/css2?family=Poppins:wght@400;500;600;700;800&display=swap">
<style>
:root{
  --bg:#f6f7f9;
  --ink:#111214;
  --muted:#6b7078;
  --line:#eceef2;
  --field:#eef2fb;
  --accent:#2f6fd0;
  --star:#f07a2a;
  --footer:#1c1d1f;
  --white:#ffffff;
}
*{box-sizing:border-box;margin:0;padding:0}
html,body{width:1200px;height:645px;overflow:hidden;background:var(--bg);font-family:"Poppins",sans-serif;color:var(--ink)}
.board{display:flex;gap:18px;padding:22px 24px;height:645px}
.screen{width:220px;height:601px;background:var(--white);border-radius:18px;box-shadow:0 8px 28px rgba(20,30,50,.08);overflow:hidden;display:flex;flex-direction:column;padding:14px}
.topbar{display:flex;justify-content:space-between;align-items:center;margin-bottom:10px}
.brand{display:flex;align-items:center;gap:5px;font-size:11px;font-weight:600;color:var(--accent)}
.brand-dot{width:9px;height:9px;border-radius:50%;background:var(--accent)}
.menu-btn{width:26px;height:26px;border-radius:7px;background:var(--ink);display:grid;place-items:center}
.search{background:var(--bg);border-radius:20px;padding:8px 12px;font-size:9px;display:flex;gap:6px;align-items:center;margin-bottom:10px}
.hero{border-radius:12px;background:linear-gradient(180deg,#5d7fa6 0%,#8fa6bf 45%,#3f5a78 100%);padding:14px 10px;color:var(--white);text-align:center;height:300px;display:flex;flex-direction:column;justify-content:space-between}
.hero small{font-size:7.5px;display:block}
.hero .rule{height:1px;background:rgba(255,255,255,.6);width:70%;margin:5px auto}
.hero h1{font-size:21px;font-weight:800;line-height:1.1;text-transform:uppercase}
.hero p{font-size:7.5px;line-height:1.5;margin-top:6px}
.btn{display:inline-block;background:var(--ink);color:var(--white);border-radius:20px;font-size:8.5px;font-weight:600;padding:9px 16px;text-align:center}
.btn.wide{display:block;width:100%}
.form{margin-top:10px;display:flex;flex-direction:column;gap:5px}
.form label{font-size:7.5px;color:var(--muted)}
.field{background:var(--field);border-radius:6px;padding:7px 9px;font-size:8px;display:flex;justify-content:space-between}
.section-title{font-size:15px;font-weight:800;text-transform:uppercase;text-align:center;line-height:1.15;margin:4px 0 6px}
.lead{font-size:7.5px;text-align:center;color:var(--ink);line-height:1.5;margin-bottom:10px}
.photo{border-radius:10px}
.card{border:1px solid var(--line);border-radius:12px;padding:8px;margin-bottom:10px}
.card h3{font-size:11.5px;font-weight:600;margin:7px 0 4px;display:flex;justify-content:space-between;align-items:center}
.card h3 span{font-size:8px;font-weight:500;color:var(--muted)}
.meta{display:flex;justify-content:space-between;font-size:7.5px;color:var(--accent);border-top:1px solid var(--line);border-bottom:1px solid var(--line);padding:5px 0;margin:4px 0}
.desc{font-size:7.5px;color:var(--muted);line-height:1.45;margin-bottom:6px}
.price-row{display:flex;justify-content:space-between;align-items:center}
.price{font-size:14px;font-weight:700}
.quote-mark{font-size:34px;font-weight:800;color:var(--accent);line-height:.8;text-align:right}
.quote{font-size:8px;font-style:italic;color:var(--muted);line-height:1.55;margin:6px 0 10px}
.reviewer{display:flex;align-items:center;gap:8px}
.avatar{width:30px;height:30px;border-radius:50%;background:linear-gradient(135deg,#c9b8a8,#7f93a8)}
.reviewer b{font-size:10px;display:block}
.reviewer i{font-size:7.5px;color:var(--muted)}
.stars{color:var(--star);font-size:9px;letter-spacing:1px}
.nav-arrows{display:flex;gap:6px;justify-content:flex-end;margin-top:8px}
.arrow{width:22px;height:22px;border-radius:50%;display:grid;place-items:center;border:1px solid var(--line)}
.arrow.on{background:var(--accent);border-color:var(--accent)}
.thumbs{display:flex;gap:6px;margin-top:8px;align-items:center}
.thumb{width:40px;height:40px;border-radius:8px;background:linear-gradient(135deg,#9fb4c8,#e7dccf)}
.newsletter{border-radius:12px;background:linear-gradient(180deg,#8c9db2,#3d5e86);color:var(--white);padding:16px 12px;height:310px;display:flex;flex-direction:column}
.newsletter h2{font-size:17px;font-weight:800;text-transform:uppercase;line-height:1.12;text-align:center}
.newsletter p{font-size:7.5px;line-height:1.5;text-align:center;margin:10px 0}
.email{background:var(--white);border-radius:20px;color:var(--muted);font-size:8px;padding:9px 12px;margin-bottom:6px}
.btn.light{background:var(--white);color:var(--ink)}
.footer{background:var(--footer);color:#c9cbd0;border-radius:12px;margin-top:10px;padding:12px;flex:1;font-size:8px}
.footer h4{color:var(--white);font-size:10px;font-weight:600;margin:6px 0 4px}
.footer ul{list-style:none;display:flex;flex-direction:column;gap:3px}
.footer .copy{border-top:1px solid #3a3b3e;margin-top:8px;padding-top:6px;text-align:center;font-size:7.5px}
</style>
</head>
<body>
<main class="board">

  <section class="screen home">
    <header class="topbar">
      <div class="brand"><span class="brand-dot"></span>Polarine</div>
      <div class="menu-btn"><svg width="12" height="10" viewBox="0 0 12 10"><path d="M1 1h10M1 5h10M4 9h7" stroke="#fff" stroke-width="1.4" stroke-linecap="round"/></svg></div>
    </header>
    <div class="search"><svg width="9" height="9" viewBox="0 0 10 10"><circle cx="4.2" cy="4.2" r="3.2" fill="none" stroke="#111" stroke-width="1.2"/><path d="M6.6 6.6 9 9" stroke="#111" stroke-width="1.2"/></svg>Search Cruise Destination</div>
    <div class="hero" role="img" aria-label="Cruise ship on calm sea">
      <div><small>Special Offers Available!</small><div class="rule"></div><small>January 2025 - April 2025</small></div>
      <div><h1>Luxury<br>Awaits You</h1><p>Explore the world's best destinations aboard the finest ships. Book your dream cruise today.</p></div>
      <span class="btn wide">Start Your Journey</span>
    </div>
    <div class="form">
      <label>Cruising to</label><div class="field">Anywhere</div>
      <label>Date</label><div class="field">Select Date<span>▾</span></div>
      <label>Guest</label><div class="field">Select Guest</div>
      <span class="btn wide">Search Cruise</span>
    </div>
  </section>

  <section class="screen deals">
    <h2 class="section-title">Unbeatable Cruise Deals</h2>
    <p class="lead">Discover Exclusive Offers And Embark On A Luxurious Adventure Without Breaking The Bank. Check Out Our Best Deals Below And Set Sail On The Journey Of A Lifetime.</p>
    <article class="card">
      <div class="photo" role="img" aria-label="Expedition ship among Antarctic ice" style="height:150px;background:linear-gradient(160deg,#dfe5ea,#7d8c99)"></div>
      <h3>Best Antarctic Cruises <span>★ 4.8</span></h3>
      <div class="meta"><span>85″ ft</span><span>6 Guest</span><span>5 Crew</span></div>
      <p class="desc">Experience the untouched beauty of Antarctica. Navigate through massive glac...</p>
      <div class="price-row"><span class="price">$4,499</span><span class="btn">Book Now</span></div>
    </article>
    <article class="card">
      <div class="photo" role="img" aria-label="Cruise ship by tropical islands" style="height:120px;background:linear-gradient(160deg,#3fb7c9,#1e6f8a)"></div>
      <h3>Galápagos Cruises <span>★ 4.8</span></h3>
    </article>
  </section>

  <section class="screen lines">
    <h2 class="section-title">Cruise With The Best In The Business</h2>
    <p class="lead">Choose From Our Premium Cruise Lines For A Top-Tier Experience. Whether You're Seeking Luxury, Adventure, Or Relaxation, We Have The Right Cruise For You.</p>
    <article class="card">
      <div class="photo" role="img" aria-label="Large cruise ship docked at port" style="height:140px;background:linear-gradient(160deg,#a9c9e8,#2d5e8f)"></div>
      <h3>Meridian Seaways</h3>
      <p class="desc">Known for groundbreaking ships and exceptional service, Meridian Seaways offer...</p>
      <span class="btn">Learn More</span>
    </article>
    <article class="card">
      <div class="photo" role="img" aria-label="Travelers relaxing on a ship deck" style="height:120px;background:linear-gradient(160deg,#9ad1e6,#c9b59a)"></div>
      <h3>Halcyon Cruises</h3>
      <p class="desc">Elevate your cruise experience with Halcyon, offering modern luxury and imp...</p>
      <span class="btn">Learn More</span>
    </article>
  </section>

  <section class="screen reviews">
    <div class="quote-mark">”</div>
    <p class="quote">The accommodation was stunning and a five-star staff went above and beyond to make every moment special. I have already booked my next cruise!</p>
    <div class="reviewer">
      <div class="avatar" role="img" aria-label="Reviewer portrait"></div>
      <div><b>Elena M</b><i>Verified Traveler</i><div class="stars">★★★★★</div></div>
    </div>
    <div class="nav-arrows">
      <span class="arrow"><svg width="8" height="8" viewBox="0 0 8 8"><path d="M5 1 2 4l3 3" fill="none" stroke="#999" stroke-width="1.2"/></svg></span>
      <span class="arrow on"><svg width="8" height="8" viewBox="0 0 8 8"><path d="M3 1l3 3-3 3" fill="none" stroke="#fff" stroke-width="1.2"/></svg></span>
    </div>
    <div class="photo" role="img" aria-label="Traveler on a sailing boat" style="height:200px;margin-top:18px;background:linear-gradient(160deg,#9cc0db,#e3ddd2)"></div>
    <div class="thumbs">
      <span class="arrow"><svg width="8" height="8" viewBox="0 0 8 8"><path d="M5 1 2 4l3 3" fill="none" stroke="#999" stroke-width="1.2"/></svg></span>
      <div class="thumb" role="img" aria-label="Travel photo"></div>
      <div class="thumb" role="img" aria-label="Travel photo"></div>
      <span class="arrow on"><svg width="8" height="8" viewBox="0 0 8 8"><path d="M3 1l3 3-3 3" fill="none" stroke="#fff" stroke-width="1.2"/></svg></span>
    </div>
    <div class="photo" role="img" aria-label="Aerial view of cruise port" style="height:120px;margin-top:14px;background:linear-gradient(160deg,#1fa5c5,#2a6d8e)"></div>
  </section>

  <section class="screen closing">
    <div class="newsletter" role="img" aria-label="City skyline backdrop">
      <h2>Stay Updated With The Latest Cruise Deals</h2>
      <p>Sign Up For Our Newsletter To Receive Exclusive Offers, The Latest News, And Helpful Travel Tips Straight To Your Inbox. Plus, Get The Option To Contact Us Instantly Via Live Chat.</p>
      <div class="email">Enter Your Email</div>
      <span class="btn light wide">Subscribe Now</span>
    </div>
    <footer class="footer">
      <h4>Community</h4>
      <ul><li>Home</li><li>Cruise Lines</li><li>Destinations</li><li>Itineraries</li><li>Blog</li></ul>
      <h4>Useful Link</h4>
      <ul><li>Upcoming Event</li><li>Book A Ticket</li><li>Travel with Us</li></ul>
      <p class="copy">Copyright © 2025 Polarine<br>All rights reserved.</p>
    </footer>
  </section>

</main>
</body>
</html>
```